Moravel Aesthetic Doctor

I require an elegant, luxurious looking business card for my aesthetic business. I am a doctor and that will set me aside from competitors. I am planning to provide home and spa based treatments to clients with high expectations. I have attached my logo.

```html
<!DOCTYPE html>
<html lang="en">
<head>
<meta charset="utf-8">
<title>Moravel Aesthetic Doctor – Business Card</title>
<link rel="stylesheet" href="https://fonts.googleapis.com/css2?family=Poppins:wght@300;400;500&display=swap">
<style>
  :root {
    --stage: #2b2b30;
    --card: #ffffff;
    --ink: #2f3237;
    --accent: #4eb2e6;
    --accent-soft: #e3f2fb;
    --wave-a: #f4fafe;
    --wave-b: #e2f1fb;
  }
  * { margin: 0; padding: 0; box-sizing: border-box; }
  html, body {
    width: 1200px; height: 800px; overflow: hidden;
    background: var(--stage);
    font-family: "Poppins", sans-serif;
  }
  .stage {
    position: relative; width: 1200px; height: 800px;
    display: flex; align-items: center; justify-content: center; gap: 48px;
  }
  .card {
    position: relative; width: 520px; height: 300px;
    background: var(--card); border-radius: 18px; overflow: hidden;
    box-shadow: 0 18px 40px rgba(0,0,0,.45);
  }

  /* Front */
  .card-front__waves {
    position: absolute; inset: 0;
    background:
      radial-gradient(ellipse 60% 90% at 15% 80%, var(--wave-b), transparent 70%),
      radial-gradient(ellipse 55% 80% at 85% 20%, var(--wave-b), transparent 70%),
      linear-gradient(135deg, var(--wave-a), #ffffff 50%, var(--wave-a));
  }
  .brand {
    position: absolute; inset: 0;
    display: flex; align-items: center; justify-content: center; gap: 18px;
  }
  .brand__dot {
    width: 58px; height: 58px; border-radius: 50%;
    background: var(--accent);
  }
  .brand__name {
    color: var(--accent); font-weight: 300;
    line-height: 1.05; text-transform: uppercase;
  }
  .brand__name .word { display: block; font-size: 46px; letter-spacing: 6px; }
  .brand__name .sub { display: block; font-size: 15px; letter-spacing: 3px; margin-top: 4px; }

  /* Back */
  .card-back { padding: 44px 36px 0 40px; color: var(--ink); }
  .holder__name { font-size: 22px; font-weight: 400; }
  .holder__post { font-size: 10px; color: var(--accent); margin-left: 4px; font-weight: 400; }
  .holder__qual { font-size: 12px; color: var(--accent); margin-top: 2px; }
  .divider {
    height: 1px; background: var(--accent);
    margin: 12px -36px 14px 0;
  }
  .contact-row { display: flex; align-items: flex-start; justify-content: space-between; width: 330px; }
  .contact { list-style: none; }
  .contact li {
    display: flex; align-items: center; gap: 9px;
    font-size: 11.5px; line-height: 22px;
  }
  .contact svg { width: 15px; height: 15px; flex: none; }
  .social { display: flex; gap: 7px; margin-top: -6px; }
  .social span { width: 18px; height: 18px; border-radius: 50%; background: var(--accent); }
  .services { margin-top: 12px; font-size: 11.5px; line-height: 18px; }
</style>
</head>
<body>
<main class="stage">

  <section class="card card-front" aria-label="Card front">
    <div class="card-front__waves" role="img" aria-label="Soft pale blue flowing wave pattern"></div>
    <div class="brand">
      <span class="brand__dot"></span>
      <h1 class="brand__name"><span class="word">Moravel</span><span class="sub">Aesthetic Doctor</span></h1>
    </div>
  </section>

  <section class="card card-back" aria-label="Card back">
    <h2 class="holder__name">Dr Elena Varsk<span class="holder__post">MRCPCH MD</span></h2>
    <p class="holder__qual">Australasian Diploma of Aesthetic Medicine</p>
    <div class="divider"></div>

    <div class="contact-row">
      <ul class="contact">
        <li>
          <svg viewBox="0 0 16 16"><circle cx="8" cy="8" r="8" fill="#4eb2e6"/><path d="M5 4.5h2l.8 2-1.1.8a5 5 0 0 0 2 2l.8-1.1 2 .8v2c-3.5.3-6.8-3-6.5-6.5z" fill="#fff"/></svg>
          0800 555 019
        </li>
        <li>
          <svg viewBox="0 0 16 16"><circle cx="8" cy="8" r="8" fill="#4eb2e6"/><rect x="4" y="5.2" width="8" height="5.6" rx=".6" fill="#fff"/><path d="M4.3 5.6 8 8.4l3.7-2.8" fill="none" stroke="#4eb2e6" stroke-width=".9"/></svg>
          elena@moravel.co.nz
        </li>
        <li>
          <svg viewBox="0 0 16 16"><circle cx="8" cy="8" r="8" fill="#4eb2e6"/><g fill="none" stroke="#fff" stroke-width=".9"><circle cx="8" cy="8" r="4"/><ellipse cx="8" cy="8" rx="1.8" ry="4"/><path d="M4 8h8"/></g></svg>
          www.moravel.co.nz
        </li>
      </ul>
      <div class="social" aria-hidden="true"><span></span><span></span></div>
    </div>

    <p class="services">
      Dermal injectables - Plasma facials - Microneedling<br>
      Skin boosters - Excessive sweating<br>
      Home and Spa Based Treatments
    </p>
  </section>

</main>
</body>
</html>
```